BRIVAN 2026 Flyer for Conference

BRIVAN needs a design for a 1-page flyer that we will hand out at an upcoming event & then later post online as a pdf. There are 3 elements which need to be on the flyer:

1) A logo. This should be prominent on the design (e.g., in the middle). The flyer should use the colors that are in that logo (e.g., for accents, design elements, and/or text; not all of these have to be used):
Dark blue: #185577
Med blue: #327C9A
Teal: #4EB1C2
Light Teal: #9EDBE6

2) The conference theme -- Oceans of Knowledge: Diving into Information Literacy -- should be at the flyer's top.

3) Finally, these six tracks should be listed below the theme and the logo (it's font size should be at least a couple sizes smaller than the size used for the theme):
- Pearls of Pedagogy: Teaching Techniques that Work
- The Depth Gauge: Measuring Instructional Impact
- Techtonic Shifts: Innovation and Educational Technology
- Captain's Log: Navigating Leadership in Library Instruction
- Swimming Together: Collaborating with Others
- The Bermuda Triangle: Exploring (Seemingly) Eternal Challenges

Font styles to use
Sans Serif

Colors
0094D4
00A9DD
6FCCEA
C7EBF8
E9F6FB

Requirements
Must have
• The 3 elements listed in the description: 1) the logo, 2) the text of the theme and 3) the text for the tracks.

```html
<!DOCTYPE html>
<html lang="en">
<head>
<meta charset="utf-8">
<title>BRIVAN 2026 Conference Flyer</title>
<link href="https://fonts.googleapis.com/css2?family=Montserrat:wght@300;400;600;700;800&display=swap" rel="stylesheet">
<style>
  :root {
    --dark-blue: #185577;
    --med-blue: #327C9A;
    --teal: #4EB1C2;
    --light-teal: #9EDBE6;
    --ink: #111111;
    --paper: #ffffff;
  }
  * { margin: 0; padding: 0; box-sizing: border-box; }
  html, body { width: 770px; height: 1200px; overflow: hidden; background: var(--paper); }
  body { font-family: "Montserrat", sans-serif; color: var(--ink); }
  .flyer { position: relative; width: 770px; height: 1200px; background: var(--paper); }

  .theme-title {
    height: 96px; display: flex; align-items: flex-end; justify-content: center;
    padding-bottom: 14px; font-weight: 800; font-size: 40px; letter-spacing: 0.5px; color: var(--ink);
  }
  .theme-band {
    background: var(--dark-blue); color: var(--paper); height: 166px;
    display: flex; flex-direction: column; align-items: center; justify-content: center; text-align: center;
  }
  .theme-band .lead { font-weight: 300; font-size: 50px; line-height: 1; letter-spacing: 1px; }
  .theme-band .main { font-weight: 800; font-size: 50px; line-height: 1.08; letter-spacing: 0.5px; }

  .brand {
    height: 570px; display: flex; flex-direction: column; align-items: center; justify-content: center;
  }
  .brand-name {
    font-weight: 800; color: var(--dark-blue); font-size: 128px; line-height: 1; letter-spacing: 2px;
    text-align: center;
  }
  .brand-name .year { display: block; font-size: 84px; margin-top: 10px; }
  .brand-place {
    margin-top: 38px; font-weight: 700; font-size: 28px; letter-spacing: 5px; color: var(--teal);
  }

  .tracks {
    display: grid; grid-template-columns: 1fr 1fr; column-gap: 20px; row-gap: 22px;
    padding: 10px 40px 0 48px;
  }
  .track { display: flex; align-items: center; gap: 10px; }
  .track-icon { flex: 0 0 72px; width: 72px; height: 72px; }
  .track-name { font-weight: 700; font-size: 18px; color: var(--med-blue); line-height: 1.2; }
  .track-desc { font-weight: 600; font-size: 15.5px; color: var(--ink); line-height: 1.15; }

  .footer-band { position: absolute; left: 0; right: 0; bottom: 0; height: 40px; background: var(--dark-blue); }
</style>
</head>
<body>
<main class="flyer">
  <header>
    <h1 class="theme-title">OCEANS OF KNOWLEDGE:</h1>
    <div class="theme-band">
      <span class="lead">DIVING INTO</span>
      <span class="main">INFORMATION LITERACY</span>
    </div>
  </header>

  <section class="brand">
    <div class="brand-name">BRIVAN<span class="year">2026</span></div>
    <div class="brand-place">NORFOLK, VA · MAY 7-9</div>
  </section>

  <section class="tracks">
    <div class="track">
      <svg class="track-icon" viewBox="0 0 72 72" role="img" aria-label="Icon of a presenter at a board"><circle cx="36" cy="36" r="33" fill="var(--paper)" stroke="var(--teal)" stroke-width="3"/><circle cx="36" cy="36" r="22" fill="var(--light-teal)" opacity="0.45"/></svg>
      <div><div class="track-name">Pearls of Pedagogy:</div><div class="track-desc">Teaching Techniques<br>that Work</div></div>
    </div>
    <div class="track">
      <svg class="track-icon" viewBox="0 0 72 72" role="img" aria-label="Icon of a raised fist"><circle cx="36" cy="36" r="33" fill="var(--paper)" stroke="var(--teal)" stroke-width="3"/><circle cx="36" cy="36" r="22" fill="var(--light-teal)" opacity="0.45"/></svg>
      <div><div class="track-name">Captain's Log:</div><div class="track-desc">Navigating Leadership in<br>Library Instruction</div></div>
    </div>
    <div class="track">
      <svg class="track-icon" viewBox="0 0 72 72" role="img" aria-label="Icon of a ruler and set square"><circle cx="36" cy="36" r="33" fill="var(--paper)" stroke="var(--teal)" stroke-width="3"/><circle cx="36" cy="36" r="22" fill="var(--light-teal)" opacity="0.45"/></svg>
      <div><div class="track-name">The Depth Gauge:</div><div class="track-desc">Measuring<br>Instructional Impact</div></div>
    </div>
    <div class="track">
      <svg class="track-icon" viewBox="0 0 72 72" role="img" aria-label="Icon of two clasped hands"><circle cx="36" cy="36" r="33" fill="var(--paper)" stroke="var(--teal)" stroke-width="3"/><circle cx="36" cy="36" r="22" fill="var(--light-teal)" opacity="0.45"/></svg>
      <div><div class="track-name">Swimming Together:</div><div class="track-desc">Collaborating with Others</div></div>
    </div>
    <div class="track">
      <svg class="track-icon" viewBox="0 0 72 72" role="img" aria-label="Icon of hands holding a light bulb"><circle cx="36" cy="36" r="33" fill="var(--paper)" stroke="var(--teal)" stroke-width="3"/><circle cx="36" cy="36" r="22" fill="var(--light-teal)" opacity="0.45"/></svg>
      <div><div class="track-name">Techtonic Shifts:</div><div class="track-desc">Innovation and<br>Educational Technology</div></div>
    </div>
    <div class="track">
      <svg class="track-icon" viewBox="0 0 72 72" role="img" aria-label="Icon of a report with charts and a magnifier"><circle cx="36" cy="36" r="33" fill="var(--paper)" stroke="var(--teal)" stroke-width="3"/><circle cx="36" cy="36" r="22" fill="var(--light-teal)" opacity="0.45"/></svg>
      <div><div class="track-name">The Bermuda Triangle:</div><div class="track-desc">Exploring (Seemingly)<br>Eternal Challenges</div></div>
    </div>
  </section>

  <div class="footer-band"></div>
</main>
</body>
</html>
```